Redesign Canvas Art E-Commerce Website

Help! I hired a couple of companies on Brisklo.com to build and design an e-commerce website for me. After three long and painful months, I have one that I believe is functional on the back-end, but aesthetically on the front end is a mess.

We are a small family business that will take your digital photo and manipulate it into a digitally created oil, watercolor or impressionist style pieces of artwork that we print on museum quality, gallery grade canvas and ship to the customer, ready to hang.

We are looking to create an e-commerce website where a customer can choose their art style, upload a photo, choose their canvas size and orientation (horizontal or vertical) and checkout. Within 48 hours, we will send them back a proof of their newly created, customized artwork for them to approve or not approve. If they approve, we print, package and ship them the product. If they do not approve, we offer unlimited revisions until they are happy.

As I mentioned, the back end functionality is already there, just need design help. No coding required

Here is a link to the development page that they created: https://plumwickstudio.com/development/

As you can see, it looks off...doesnt line up properly, wasted space, weird font. Feel free to either correct the homepage they created or design an entirely new page. I am attaching some examples of before and after photos of artwork for reference. I also think the testimonials page and shop page can use a little style. The content is there and accurate, it just doesn't look pretty. Please keep in mind that our customers will probably not be very tech savvy. The customers will probably be sending us pics of kids, grandkids, pets, family portraits, vacation photos, etc.

Here is one of our competitors - www.gildavantry.com
Their website looks clean and inviting.

Thank you in advance! Im looking forward to seeing the results. I am including our logo in the attachments (I do not have it in a vector file, just a jpeg)

Target Market(s)

Non tech-savvy indiduals, 30-70 years old

Industry/Entity Type

Please look at https://plumwickstudio.com/development/ to see various pages and what the other designers did

Number of Pages Required

1 page

Requirements
Must have
• Verbiage on pages leave "as is" but feel free to change styles. Would like to keep existing four categories on homepage
Nice to have
• Warm and inviting homepage that evokes emotion

```html
<!DOCTYPE html>
<html lang="en">
<head>
<meta charset="utf-8">
<title>Hearthframe Creations – Custom Canvas Art</title>
<link href="https://fonts.googleapis.com/css2?family=Archivo+Black&family=Roboto:wght@400;500;700&family=Roboto+Condensed:wght@700&display=swap" rel="stylesheet">
<style>
  :root {
    --orange: #f47c20;
    --salmon: #f0a08f;
    --salmon-block: #f4a594;
    --ink: #1a1a1a;
    --body: #3a3a3a;
    --band: #ececec;
    --white: #ffffff;
    --black: #000000;
    --gold-1: #b8923e;
    --gold-2: #e5c774;
    --gold-3: #8a6a25;
  }
  * { box-sizing: border-box; margin: 0; padding: 0; }
  html, body { width: 1200px; height: 4329px; overflow: hidden; }
  body {
    position: relative;
    background: var(--white);
    font-family: "Roboto", Arial, sans-serif;
    color: var(--ink);
  }

  /* Top strip */
  .promo-bar {
    position: absolute; left: 0; top: 0; width: 1200px; height: 37px;
    background: var(--orange); color: var(--white);
    font-size: 15px; line-height: 37px; text-align: center;
  }

  /* Header */
  .brand {
    position: absolute; left: 97px; top: 64px;
    display: flex; align-items: center; gap: 10px;
    font-size: 30px; font-weight: 700; color: var(--ink);
  }
  .brand-dot { width: 26px; height: 26px; border-radius: 50%; background: var(--orange); }
  .main-nav a {
    position: absolute; top: 84px; font-size: 15px; color: var(--ink);
    text-decoration: none; transform: translateX(-50%);
  }
  .cart-icon { position: absolute; left: 1072px; top: 84px; }

  /* Hero */
  .hero {
    position: absolute; left: 99px; top: 148px; width: 1002px; height: 481px;
    border-radius: 22px;
    background: linear-gradient(135deg, #d9d9d9 0%, #c9c9c9 45%, #dadada 100%);
  }
  .hero-title {
    position: absolute; left: 41px; top: 110px; z-index: 2;
    width: 490px; white-space: nowrap;
    font-family: "Archivo Black", "Arial Black", sans-serif;
    font-size: 31px; line-height: 47px; letter-spacing: -0.6px; color: #111;
  }
  .btn {
    position: absolute; display: block; background: var(--orange); color: var(--white);
    border-radius: 6px; text-align: center; text-decoration: none; font-size: 20px;
  }
  .hero .btn { left: 42px; top: 274px; width: 180px; height: 54px; line-height: 54px; }
  .hero-art-frame {
    position: absolute; left: 535px; top: 101px; width: 437px; height: 286px;
    background: linear-gradient(135deg, var(--gold-2), var(--gold-1) 50%, var(--gold-3));
  }
  .hero-art {
    position: absolute; left: 22px; top: 22px; right: 22px; bottom: 22px;
    background: linear-gradient(180deg, #5f8fd0 0%, #6fa07a 45%, #3f6e4c 70%, #6a6f86 100%);
  }

  /* Section headings */
  .section-title {
    position: absolute; left: 0; width: 1200px; text-align: center;
    font-family: "Roboto Condensed", "Arial Narrow", sans-serif; font-weight: 700; color: var(--ink);
  }

  /* Categories */
  .category-img { position: absolute; width: 487px; height: 271px; border-radius: 4px; }
  .cat-oil { background: linear-gradient(135deg, #3d5a2a, #8b2f22 40%, #e8e2d6 65%, #4b6b30); }
  .cat-watercolor { background: linear-gradient(135deg, #f4efe9, #e9cbb7 50%, #fafafa); }
  .cat-impressionist { background: linear-gradient(180deg, #c9d9e6 0%, #b06a52 30%, #3ec2b0 55%, #1d4f7a 100%); }
  .cat-digital { background: linear-gradient(135deg, #c9d6a5, #f1efea 45%, #6d9b58 100%); }
  .category-name { position: absolute; font-size: 34px; color: var(--ink); line-height: 40px; }
  .category-btn { width: 145px; height: 47px; line-height: 47px; font-size: 20px; }

  /* Why us */
  .why-band { position: absolute; left: 0; top: 1647px; }
  .feature { position: absolute; top: 1803px; width: 310px; text-align: center; }
  .feature-icon { display: block; margin: 0 auto; }
  .feature h3 { margin-top: 30px; font-size: 25px; font-weight: 500; color: var(--ink); }
  .feature p { margin-top: 12px; font-size: 15.5px; line-height: 26px; color: var(--body); }

  /* Showcase */
  .showcase-frame {
    position: absolute; left: 185px; top: 2454px; width: 829px; height: 538px;
    background: linear-gradient(135deg, var(--gold-2), var(--gold-1) 45%, var(--gold-3) 100%);
  }
  .showcase-photo {
    position: absolute; left: 64px; top: 59px; width: 704px; height: 420px;
    background: linear-gradient(135deg, #9ec08a 0%, #dfe6e8 45%, #3f6e3b 70%, #a9c7e4 100%);
  }
  .thumb {
    position: absolute; top: 3026px; width: 182px; height: 117px;
    background: linear-gradient(135deg, var(--gold-2), var(--gold-3));
  }
  .thumb span { position: absolute; left: 10px; top: 10px; right: 10px; bottom: 10px; }
  .thumb-1 span { background: linear-gradient(135deg, #cfd9c2, #b9a99a); }
  .thumb-2 span { background: linear-gradient(135deg, #7fb3e0, #4a3424); }
  .thumb-3 span { background: linear-gradient(135deg, #6b4a2a, #c98a4a); }
  .thumb-4 span { background: linear-gradient(135deg, #3a3a3a, #d9d2c6); }
  .carousel-arrow { position: absolute; top: 3078px; }

  /* About */
  .about-title { position: absolute; left: 102px; top: 3280px; font-size: 34px; font-weight: 700; color: var(--ink); }
  .about-copy { position: absolute; left: 99px; top: 3362px; width: 530px; font-size: 15.5px; line-height: 25px; color: var(--body); }
  .about-copy p + p { margin-top: 24px; }
  .about .btn { left: 99px; top: 3708px; width: 180px; height: 54px; line-height: 54px; }
  .about-accent { position: absolute; left: 711px; top: 3266px; width: 388px; height: 479px; background: var(--salmon-block); }
  .about-photo {
    position: absolute; left: 696px; top: 3283px; width: 388px; height: 479px;
    background: linear-gradient(160deg, #3b2a1c 0%, #7a4a2c 35%, #e3cfae 60%, #6f7a3a 100%);
  }

  /* Footer */
  .site-footer { position: absolute; left: 0; top: 3863px; width: 1200px; height: 466px; background: var(--black); color: var(--white); }
  .footer-brand {
    position: absolute; left: 0; top: 86px; width: 1200px;
    display: flex; justify-content: center; align-items: center; gap: 12px;
    font-size: 36px; font-weight: 700; color: var(--white);
  }
  .footer-brand .brand-dot { width: 30px; height: 30px; }
  .footer-nav a {
    position: absolute; top: 214px; font-size: 16px; color: var(--white);
    text-decoration: none; transform: translateX(-50%);
  }
  .contact-box { position: absolute; top: 294px; width: 48px; height: 48px; background: var(--white); display: flex; align-items: center; justify-content: center; }
  .contact-text { position: absolute; top: 306px; font-size: 17px; color: var(--white); }
  .footer-rule { position: absolute; left: 99px; top: 400px; width: 1002px; height: 1px; background: #555; }
  .copyright { position: absolute; left: 0; top: 416px; width: 1200px; text-align: center; font-size: 15px; color: var(--white); }
</style>
</head>
<body>

<div class="promo-bar">Free Shipping For All Florida &amp; Orders</div>

<header class="site-header">
  <div class="brand"><span class="brand-dot"></span>Hearthframe</div>
  <nav class="main-nav">
    <a href="#" style="left:469px">Home</a>
    <a href="#" style="left:568px">About Us</a>
    <a href="#" style="left:666px">Shop</a>
    <a href="#" style="left:750px">FAQs</a>
    <a href="#" style="left:857px">Testimonials</a>
    <a href="#" style="left:983px">Contact Us</a>
  </nav>
  <svg class="cart-icon" width="20" height="18" viewBox="0 0 20 18" aria-label="Cart">
    <path d="M0 1h4l3 10h10l2-7H6" fill="none" stroke="#f47c20" stroke-width="2.4"/>
    <circle cx="8" cy="15" r="2" fill="#f47c20"/><circle cx="16" cy="15" r="2" fill="#f47c20"/>
  </svg>
</header>

<section class="hero">
  <h1 class="hero-title">Turn Your Digital Photos<br>IntoOne of a Kind<br>Wall Art</h1>
  <a class="btn" href="#">Get Started</a>
  <div class="hero-art-frame">
    <div class="hero-art" role="img" aria-label="Painted canvas of palm trees in front of a seaside hotel, in a gold frame"></div>
  </div>
</section>

<section class="categories">
  <h2 class="section-title" style="top:730px;font-size:38px">CATEGORIES</h2>

  <div class="category-img cat-oil" style="left:99px;top:812px" role="img" aria-label="Oil painting style portrait of a bride and groom"></div>
  <div class="category-name" style="left:123px;top:1105px">Oil</div>
  <a class="btn category-btn" href="#" style="left:412px;top:1101px">Get Started</a>

  <div class="category-img cat-watercolor" style="left:612px;top:812px" role="img" aria-label="Watercolor style portrait of a mother and baby"></div>
  <div class="category-name" style="left:637px;top:1105px">Watercolor</div>
  <a class="btn category-btn" href="#" style="left:926px;top:1101px">Get Started</a>

  <div class="category-img cat-impressionist" style="left:99px;top:1194px" role="img" aria-label="Impressionist style painting of a traveler beside gondolas in Venice"></div>
  <div class="category-name" style="left:123px;top:1487px">Impressionist</div>
  <a class="btn category-btn" href="#" style="left:412px;top:1483px">Get Started</a>

  <div class="category-img cat-digital" style="left:612px;top:1194px" role="img" aria-label="Digital photo of two children eating ice cream"></div>
  <div class="category-name" style="left:637px;top:1487px">Digital Photo</div>
  <a class="btn category-btn" href="#" style="left:926px;top:1483px">Get Started</a>
</section>

<section class="why-us">
  <svg class="why-band" width="1200" height="606" viewBox="0 0 1200 606">
    <path d="M0 84 Q600 -84 1200 84 L1200 522 Q600 690 0 522 Z" fill="#ececec"/>
  </svg>
  <h2 class="section-title" style="top:1708px;font-size:33px">WHY US?</h2>

  <div class="feature" style="left:101px">
    <svg class="feature-icon" width="172" height="172" viewBox="0 0 172 172">
      <circle cx="86" cy="86" r="86" fill="#f0a08f"/>
      <g fill="none" stroke="#fff" stroke-width="4" stroke-linecap="round">
        <path d="M86 48a26 26 0 0 0-16 46c4 4 5 8 5 14h22c0-6 1-10 5-14a26 26 0 0 0-16-46z"/>
        <path d="M75 116h22M77 124h18M80 132h12"/>
        <path d="M86 22v12M50 36l7 9M122 36l-7 9M34 66l11 3M138 66l-11 3"/>
      </g>
    </svg>
    <h3>Your Idea Your Design</h3>
    <p>Each art piece is customized for you! You choose your size, orientation and art style. Makes a perfect gift!!!</p>
  </div>

  <div class="feature" style="left:445px">
    <svg class="feature-icon" width="172" height="172" viewBox="0 0 172 172">
      <circle cx="86" cy="86" r="86" fill="#f0a08f"/>
      <g fill="none" stroke="#fff" stroke-width="4" stroke-linecap="round" stroke-linejoin="round">
        <rect x="50" y="66" width="58" height="40"/>
        <path d="M108 78h18l12 14v14h-30z"/>
        <circle cx="66" cy="112" r="7"/><circle cx="122" cy="112" r="7"/>
        <circle cx="56" cy="50" r="12"/><path d="M56 43v7h5"/>
        <path d="M24 76h18M30 88h12M20 100h22"/>
      </g>
    </svg>
    <h3>Fast Shipping</h3>
    <p>Your artwork is printed and shipped in the USA! We offer fast turnaround with transit times typically 3-7 days. Free tracking with each order!!</p>
  </div>

  <div class="feature" style="left:791px">
    <svg class="feature-icon" width="172" height="172" viewBox="0 0 172 172">
      <circle cx="86" cy="86" r="86" fill="#f0a08f"/>
      <g fill="none" stroke="#fff" stroke-width="4" stroke-linejoin="round">
        <circle cx="86" cy="104" r="34"/>
        <path d="M74 100h8v24h-8zM82 102l10-16c3 0 6 2 5 7l-2 7h12c3 0 5 3 4 6l-4 14c-1 3-3 4-6 4H82"/>
        <path d="M46 38l3 7 7 1-5 5 1 7-6-3-6 3 1-7-5-5 7-1zM86 24l3 7 7 1-5 5 1 7-6-3-6 3 1-7-5-5 7-1zM126 38l3 7 7 1-5 5 1 7-6-3-6 3 1-7-5-5 7-1z"/>
      </g>
    </svg>
    <h3>High Quality</h3>
    <p>We've put a lot of effort ensuring your artwork is of the highest quality. Each piece is printed on the highest quality, gallery grade canvas. It is ready to hang upon arrival.!</p>
  </div>
</section>

<section class="showcase">
  <h2 class="section-title" style="top:2362px;font-size:33px">FROM PHOTO TO MUSEUM QUALITY CANVAS ART</h2>
  <div class="showcase-frame">
    <div class="showcase-photo" role="img" aria-label="Photo of a smiling older couple, the woman hugging the man from behind, in a gold frame"></div>
  </div>
  <svg class="carousel-arrow" style="left:96px" width="20" height="26" viewBox="0 0 20 26"><path d="M15 3L5 13l10 10" fill="none" stroke="#f47c20" stroke-width="4"/></svg>
  <div class="thumb thumb-1" style="left:195px"><span role="img" aria-label="Framed photo of an older couple"></span></div>
  <div class="thumb thumb-2" style="left:405px"><span role="img" aria-label="Framed photo of a horse and rider"></span></div>
  <div class="thumb thumb-3" style="left:615px"><span role="img" aria-label="Framed photo of a dog and a cat"></span></div>
  <div class="thumb thumb-4" style="left:825px"><span role="img" aria-label="Framed photo of a puppy"></span></div>
  <svg class="carousel-arrow" style="left:1083px" width="20" height="26" viewBox="0 0 20 26"><path d="M5 3l10 10L5 23" fill="none" stroke="#f47c20" stroke-width="4"/></svg>
</section>

<section class="about">
  <h2 class="about-title">ABOUT US</h2>
  <div class="about-copy">
    <p>At Hearthframe Creations, we take your digital photo and turn it into a one-of-a-kind piece of artwork!</p>
    <p>The process couldn't be any easier. Simply upload your photo, choose your art style and size, and let our team of skilled digital artists do the rest. Do you want to put your digital photo on canvas without an art style? No problem! Just choose the “Digital Photo/Retouching” category and upload your photo. We can print your photo “as is” or do some minor retouching (e.g. remove objects, enhance colors, lighten photo, etc)</p>
    <p>You will receive a proof in your email to approve within 1-2 days. Once approved, your customized artwork will be transferred to canvas and shipped from our design studio in Florida.</p>
  </div>
  <a class="btn" href="#">Read More</a>
  <div class="about-accent"></div>
  <div class="about-photo" role="img" aria-label="Oil painting style portrait of a bride holding a bouquet"></div>
</section>

<footer class="site-footer">
  <div class="footer-brand"><span class="brand-dot"></span>Hearthframe</div>
  <nav class="footer-nav">
    <a href="#" style="left:319px">Home</a>
    <a href="#" style="left:424px">About Us</a>
    <a href="#" style="left:526px">Shop</a>
    <a href="#" style="left:615px">FAQs</a>
    <a href="#" style="left:728px">Testimonials</a>
    <a href="#" style="left:862px">Contact Us</a>
  </nav>

  <div class="contact-box" style="left:141px">
    <svg width="24" height="18" viewBox="0 0 24 18"><rect width="24" height="18" rx="2" fill="#f47c20"/><path d="M2 3l10 7 10-7" fill="none" stroke="#fff" stroke-width="2"/></svg>
  </div>
  <div class="contact-text" style="left:205px">info@hearthframeart.com</div>

  <div class="contact-box" style="left:492px">
    <svg width="20" height="26" viewBox="0 0 20 26"><path d="M10 0a10 10 0 0 0-10 10c0 7 10 16 10 16s10-9 10-16A10 10 0 0 0 10 0z" fill="#f47c20"/><circle cx="10" cy="10" r="4" fill="#fff"/></svg>
  </div>
  <div class="contact-text" style="left:561px">Nemo enim ipsam voluptatem</div>

  <div class="contact-box" style="left:851px">
    <svg width="22" height="22" viewBox="0 0 24 24"><path d="M6.6 10.8a15 15 0 0 0 6.6 6.6l2.2-2.2c.3-.3.7-.4 1-.2 1.1.4 2.3.6 3.6.6.6 0 1 .4 1 1V20c0 .6-.4 1-1 1A17 17 0 0 1 3 4c0-.6.4-1 1-1h3.5c.6 0 1 .4 1 1 0 1.3.2 2.5.6 3.6.1.3 0 .7-.2 1z" fill="#f47c20"/></svg>
  </div>
  <div class="contact-text" style="left:919px">+1888 8888 8888</div>

  <div class="footer-rule"></div>
  <div class="copyright">Copyrights@2023 Hearthframe Creations .All Rights Reserved</div>
</footer>

</body>
</html>
```